Looking for a dynamic business card for a pizzeria.

A business card with our food, logo, and space for name, title, email, website, phone. The card should convey quality, unique, amazing. On the front, I envision food photo or photos with the owners names and contact information. On the back, more food with locations, website, facebook, twitter, instagram icons. It should look polished, not cartoonish, or plain.
Target Market(s)
upscale, local food buyers, 30-50 years in age.
Industry/Entity Type
Restaurant
Contact Information for Business Card
Business Name: Bru'nettix, LLC
Website: www.brunettix.com
Back:
2 locations: (can list on the back of card)
1. Harborview
4087 Corlan Avenue
Marlow, WA 98301
360-481-5067
2. Kelsey Ridge
7315 Wendmere Road
Marlow, WA 98317
360-293-8840
front:
EDITABLE space for
Business name
Person's Name
title
2nd title
Email address
cell-phone number
Requirements
Must have
- logo
- my food photo or photos (no watermarks showing)
- locations on back
- Person contact information on front
- full bleed

```html
<!DOCTYPE html>
<html lang="en">
<head>
<meta charset="utf-8">
<title>Bru'nettix Business Card</title>
<link rel="stylesheet" href="https://fonts.googleapis.com/css2?family=Questrial&display=swap">
<style>
  :root {
    --bg: #e9e6e1;
    --card: #ffffff;
    --red: #c4161c;
    --green: #2f6b2f;
    --ink: #3a3a3a;
    --dough-light: #e6d3bd;
    --dough-mid: #b89676;
    --dough-dark: #4a403a;
  }
  * { margin: 0; padding: 0; box-sizing: border-box; }
  html, body {
    width: 1200px; height: 843px; overflow: hidden;
    background: var(--bg);
    font-family: "Questrial", sans-serif;
  }
  .canvas { position: relative; width: 1200px; height: 843px; }
  .card {
    position: absolute; left: 290px; width: 620px; height: 354px;
    overflow: hidden; box-shadow: 0 6px 18px rgba(0,0,0,.18);
  }
  /* Back side */
  .card--back { top: 45px; }
  .back-photo {
    position: absolute; inset: 0;
    background:
      radial-gradient(ellipse 38% 48% at 48% 58%, var(--dough-light) 0%, var(--dough-mid) 60%, transparent 100%),
      radial-gradient(ellipse 30% 30% at 80% 45%, #c79a82 0%, transparent 100%),
      linear-gradient(120deg, #8a8580 0%, var(--dough-dark) 55%, #2e2a27 100%);
  }
  .back-brand {
    position: absolute; left: 36px; top: 66px;
    color: #ffffff; font-size: 32px; letter-spacing: .5px;
  }
  .social { position: absolute; right: 28px; top: 22px; display: flex; gap: 10px; }
  .social span { width: 14px; height: 14px; background: var(--red); }

  /* Front side */
  .card--front { top: 444px; background: linear-gradient(180deg, #ffffff 0%, #f2f2f2 100%); }
  .front-brand {
    position: absolute; left: 40px; top: 34px;
    color: var(--ink); font-size: 40px; letter-spacing: .5px;
  }
  .title-flag { position: absolute; right: 22px; top: 28px; width: 230px; height: 210px; }
  .title-flag .person {
    position: absolute; top: 56px; width: 100%; text-align: center; color: #fff;
  }
  .person-name { font-size: 20px; letter-spacing: .5px; }
  .person-role { font-size: 15px; margin-top: 3px; }
  .locations {
    position: absolute; left: 40px; top: 118px;
    font-size: 17px; line-height: 20px; color: var(--ink);
  }
  .location-name, .label { color: var(--green); }
  .location + .location { margin-top: 4px; }
  .contacts {
    position: absolute; left: 316px; top: 254px;
    font-size: 17px; line-height: 25px; color: var(--ink);
    list-style: none;
  }
  .contacts li { display: flex; align-items: center; gap: 10px; }
  .contacts svg { width: 14px; height: 14px; flex: none; }
</style>
</head>
<body>
<main class="canvas">

  <section class="card card--back" aria-label="Card back">
    <div class="back-photo" role="img" aria-label="Photo of hands shaping pizza dough dusted with flour"></div>
    <div class="back-brand">Bru'nettix</div>
    <div class="social" aria-label="Social links"><span></span><span></span></div>
  </section>

  <section class="card card--front" aria-label="Card front">
    <div class="front-brand">Bru'nettix</div>

    <div class="title-flag">
      <svg width="230" height="210" viewBox="0 0 230 210">
        <polygon points="0,0 230,0 230,130 90,210 0,150" fill="var(--red)"/>
      </svg>
      <div class="person">
        <div class="person-name">ELENA MARCHETTI</div>
        <div class="person-role">Founder</div>
      </div>
    </div>

    <div class="locations">
      <div class="location">
        <div class="location-name">Harborview</div>
        <div>4087 Corlan Avenue</div>
        <div>Marlow, WA 98301</div>
        <div><span class="label">Phone:</span>360-481-5067</div>
      </div>
      <div class="location">
        <div class="location-name">Kelsey Ridge</div>
        <div>7315 Wendmere Road</div>
        <div>Marlow, WA 98317</div>
        <div><span class="label">Phone:</span>360-293-8840</div>
      </div>
    </div>

    <ul class="contacts">
      <li>
        <svg viewBox="0 0 14 14"><rect x="3" y="0.5" width="8" height="13" rx="1.5" fill="none" stroke="var(--green)" stroke-width="1.4"/><circle cx="7" cy="11" r="0.9" fill="var(--green)"/></svg>
        689 514 7720
      </li>
      <li>
        <svg viewBox="0 0 14 14"><rect x="0.5" y="2.5" width="13" height="9" fill="var(--green)"/><polyline points="0.5,2.5 7,8 13.5,2.5" fill="none" stroke="#fff" stroke-width="1.2"/></svg>
        name@brunettix.com
      </li>
      <li>
        <svg viewBox="0 0 14 14"><circle cx="7" cy="7" r="6.3" fill="none" stroke="var(--green)" stroke-width="1.3"/><ellipse cx="7" cy="7" rx="2.6" ry="6.3" fill="none" stroke="var(--green)" stroke-width="1"/><line x1="0.7" y1="7" x2="13.3" y2="7" stroke="var(--green)" stroke-width="1"/></svg>
        www.brunettix.com
      </li>
    </ul>
  </section>

</main>
</body>
</html>
```